Business Card for a New Zealand IT Startup

I need a business card for VELTA Holdings. We are a young startup based in New Zealand working in internet marketing and web development. The design should have some element connected to New Zealand, such as wave, koru or silver fern, just don't use a kiwi bird.

```html
<!DOCTYPE html>
<html lang="en">
<head>
<meta charset="utf-8">
<title>VELTA Holdings – Business Card</title>
<link rel="stylesheet" href="https://fonts.googleapis.com/css2?family=Open+Sans:wght@400;600;700&display=swap">
<style>
  :root {
    --bg: #2e2f31;
    --brand-blue: #0f6cbf;
    --brand-blue-dark: #0a5aa3;
    --wave-light: #3d8ad0;
    --wave-pale: #e3edf7;
    --accent-orange: #e2572a;
    --paper: #ffffff;
    --ink: #2b2b2b;
  }
  * { box-sizing: border-box; margin: 0; padding: 0; }
  html, body { width: 1200px; height: 1000px; overflow: hidden; }
  body {
    background: var(--bg);
    font-family: "Open Sans", Arial, sans-serif;
    position: relative;
  }
  .card {
    position: absolute;
    width: 580px;
    height: 331px;
    border-radius: 2px;
    overflow: hidden;
  }
  .card-back {
    left: 540px;
    top: 110px;
    background: linear-gradient(135deg, var(--brand-blue) 0%, var(--brand-blue-dark) 100%);
  }
  .card-front {
    left: 80px;
    top: 540px;
    background: var(--paper);
  }
  .wave {
    position: absolute;
    left: 0;
    bottom: 0;
    width: 580px;
    display: block;
  }
  .wave-back { height: 90px; }
  .wave-front { height: 64px; }
  .wave-back .wave-fill { fill: var(--wave-light); opacity: 0.35; }
  .wave-back .wave-line { fill: none; stroke: var(--paper); stroke-width: 1.5; opacity: 0.35; }
  .wave-front .wave-pale { fill: var(--wave-pale); }
  .wave-front .wave-fill { fill: var(--brand-blue); }
  .name-tab {
    position: absolute;
    left: 0; top: 0;
    width: 14px; height: 32px;
    background: var(--brand-blue);
  }
  .holder {
    position: absolute;
    left: 30px; top: 16px;
  }
  .holder-name {
    color: var(--brand-blue);
    font-weight: 700;
    font-size: 19px;
    letter-spacing: 0.5px;
    line-height: 1.15;
  }
  .holder-role {
    color: var(--accent-orange);
    font-size: 15px;
    line-height: 1.2;
  }
  .address {
    position: absolute;
    left: 30px; top: 106px;
    color: var(--ink);
    font-size: 15px;
    line-height: 1.3;
  }
  .contact-list {
    position: absolute;
    left: 14px; top: 160px;
    list-style: none;
    color: var(--ink);
    font-size: 15px;
    line-height: 1.42;
  }
  .contact-list li { display: flex; align-items: center; gap: 8px; }
  .contact-list svg { width: 14px; height: 14px; fill: var(--brand-blue); flex: none; }
  .wordmark {
    position: absolute;
    display: flex;
    align-items: center;
    gap: 14px;
    font-weight: 700;
  }
  .card-back .wordmark { right: 48px; bottom: 96px; color: var(--paper); }
  .card-front .wordmark { right: 40px; bottom: 72px; color: var(--brand-blue); }
  .wordmark-text {
    font-size: 40px;
    line-height: 1;
    letter-spacing: 2px;
  }
  .wordmark-text span { display: block; font-size: 22px; letter-spacing: 8px; margin-top: 4px; }
  .wordmark-dot {
    width: 44px; height: 44px;
    border-radius: 50%;
    background: currentColor;
  }
</style>
</head>
<body>

  <section class="card card-back" aria-label="Business card back">
    <svg class="wave wave-back" viewBox="0 0 580 90" preserveAspectRatio="none" aria-hidden="true">
      <path class="wave-fill" d="M0 46 C 100 16, 200 70, 300 44 S 490 18, 580 40 L580 90 L0 90 Z"/>
      <path class="wave-line" d="M0 30 C 110 6, 210 56, 310 30 S 500 8, 580 26"/>
    </svg>
    <div class="wordmark">
      <div class="wordmark-text">VELTA<span>HOLDINGS</span></div>
      <div class="wordmark-dot"></div>
    </div>
  </section>

  <section class="card card-front" aria-label="Business card front">
    <div class="name-tab"></div>
    <div class="holder">
      <p class="holder-name">MARA TANE</p>
      <p class="holder-role">PRESIDENT</p>
    </div>
    <p class="address">41 Harbour View Road<br>Wellington 6011, NZ</p>
    <ul class="contact-list">
      <li>
        <svg viewBox="0 0 16 16" aria-hidden="true"><path d="M3 1h3l1.5 4-2 1.3a9 9 0 0 0 4.2 4.2L11 8.5l4 1.5v3a2 2 0 0 1-2 2C6.9 15 1 9.1 1 3a2 2 0 0 1 2-2z"/></svg>
        555 0142 7781
      </li>
      <li>
        <svg viewBox="0 0 16 16" aria-hidden="true"><path d="M4.5 0h7A1.5 1.5 0 0 1 13 1.5v13a1.5 1.5 0 0 1-1.5 1.5h-7A1.5 1.5 0 0 1 3 14.5v-13A1.5 1.5 0 0 1 4.5 0zM5 2v10h6V2zm3 11a1 1 0 1 0 0 2 1 1 0 0 0 0-2z"/></svg>
        555 0198 3360
      </li>
      <li>
        <svg viewBox="0 0 16 16" aria-hidden="true"><path d="M4 1h6l2 2v3h2a1 1 0 0 1 1 1v6a1 1 0 0 1-1 1H2a1 1 0 0 1-1-1V7a1 1 0 0 1 1-1h2zm1 1v4h6V3.5L9.5 2zM4 10v2h8v-2z"/></svg>
        555 0127 4409
      </li>
      <li>
        <svg viewBox="0 0 16 16" aria-hidden="true"><path d="M1 3h14v1.2L8 9 1 4.2zM1 5.6l7 4.8 7-4.8V13H1z"/></svg>
        mara@veltaholdings.com
      </li>
      <li>
        <svg viewBox="0 0 16 16" aria-hidden="true"><path d="M8 0a8 8 0 1 0 0 16A8 8 0 0 0 8 0zm0 1.5c.9 0 2.2 2 2.5 5.5h-5C5.8 3.5 7.1 1.5 8 1.5zM5.5 9h5c-.3 3.5-1.6 5.5-2.5 5.5S5.8 12.5 5.5 9z"/></svg>
        www.veltaholdings.com
      </li>
    </ul>
    <div class="wordmark">
      <div class="wordmark-text">VELTA<span>HOLDINGS</span></div>
      <div class="wordmark-dot"></div>
    </div>
    <svg class="wave wave-front" viewBox="0 0 580 64" preserveAspectRatio="none" aria-hidden="true">
      <path class="wave-pale" d="M0 30 C 110 6, 220 46, 320 26 S 500 4, 580 20 L580 64 L0 64 Z"/>
      <path class="wave-fill" d="M0 42 C 100 24, 210 58, 320 40 S 500 22, 580 34 L580 64 L0 64 Z"/>
    </svg>
  </section>

</body>
</html>
```